Classy, Elegant, Simple Business Card Design

Looking to have a classy, simple, and elegant design. Want a top notch designed business card. I really like the look of the new torvane credit card. I also like the design I attached. I am trying to reach 21-29 year old females for booking us for there wedding or event. We offer Disc Jockey Service, Photo Booth Rentals, and Uplighting .

Target Market(s)

21-28 year old females

Contact Information for Business Card

Has to have logo, website, email, and phone number

Font styles to use
Other font styles liked:
• open to font choice, modern, clean
Designer to choose
33a6d7
0791cd
0555a3
ffffff

Requirements
Must have
• Has to have logo, website, email, and phone number
Nice to have
• I really like the design of the new torvane credit card. I also included my logo and some designs I like
Should not have
• clutter or too much info

```html
<!DOCTYPE html>
<html lang="en">
<head>
<meta charset="utf-8">
<title>Tidewell Event Group – Business Card</title>
<link rel="stylesheet" href="https://fonts.googleapis.com/css2?family=Lato:wght@400;700&display=swap">
<style>
  :root {
    --backdrop: #2b2b2d;
    --card: #111113;
    --card-edge: #1a1a1d;
    --blue-light: #33a6d7;
    --blue: #0791cd;
    --blue-deep: #0555a3;
    --white: #ffffff;
    --grey-text: #c9c9cc;
    --rule: #4a4a4e;
  }
  * { box-sizing: border-box; margin: 0; padding: 0; }
  html, body {
    width: 1200px; height: 900px; overflow: hidden;
    background: var(--backdrop);
    font-family: "Lato", sans-serif;
  }
  .canvas {
    width: 1200px; height: 900px;
    display: flex; flex-direction: column; align-items: center; justify-content: center;
    gap: 50px;
  }
  .card {
    position: relative;
    width: 600px; height: 343px;
    background: linear-gradient(160deg, var(--card-edge), var(--card) 60%);
    box-shadow: 0 14px 30px rgba(0,0,0,.45);
    overflow: hidden;
    display: flex; flex-direction: column; align-items: center; justify-content: center;
  }
  .card__edge {
    position: absolute; left: 0; right: 0; bottom: 0; height: 7px;
    background: linear-gradient(90deg, var(--blue-deep), var(--blue-light) 45%, var(--blue) 70%, var(--blue-deep));
  }
  .brand-name {
    color: var(--blue);
    font-weight: 700;
    letter-spacing: 3px;
    text-transform: uppercase;
    text-align: center;
    line-height: 1.15;
  }
  .card--front .brand-name { font-size: 34px; }
  .card--back .brand-name { font-size: 24px; margin-top: -6px; }
  .divider {
    display: flex; align-items: center; gap: 8px;
    width: 180px; margin: 12px 0 8px;
  }
  .divider::before, .divider::after {
    content: ""; flex: 1; height: 1px; background: var(--rule);
  }
  .contact-icons { display: flex; gap: 5px; }
  .contact-icons svg { width: 18px; height: 18px; display: block; }
  .contact-list {
    list-style: none; text-align: center;
    color: var(--grey-text); font-size: 15px; line-height: 1.4;
  }
  .rule {
    width: 180px; height: 1px; background: var(--rule); margin: 10px 0 14px;
  }
  .services {
    color: var(--white); font-size: 16px; letter-spacing: .3px;
  }
</style>
</head>
<body>
<main class="canvas">

  <section class="card card--front" aria-label="Card front">
    <p class="brand-name">Tidewell<br>Event Group</p>
    <div class="card__edge"></div>
  </section>

  <section class="card card--back" aria-label="Card back">
    <p class="brand-name">Tidewell Event Group</p>

    <div class="divider">
      <div class="contact-icons">
        <svg viewBox="0 0 20 20" aria-label="Phone"><circle cx="10" cy="10" r="10" fill="var(--blue)"/><path d="M6.5 5.5l2 0 1 2.5-1.3 1a6 6 0 0 0 2.8 2.8l1-1.3 2.5 1v2a1 1 0 0 1-1 1A8 8 0 0 1 5.5 6.5a1 1 0 0 1 1-1z" fill="var(--white)"/></svg>
        <svg viewBox="0 0 20 20" aria-label="Email"><circle cx="10" cy="10" r="10" fill="var(--blue)"/><rect x="5" y="6.5" width="10" height="7" fill="var(--white)"/><path d="M5 6.5l5 4 5-4" fill="none" stroke="var(--blue)" stroke-width="1"/></svg>
        <svg viewBox="0 0 20 20" aria-label="Website"><circle cx="10" cy="10" r="10" fill="var(--blue)"/><circle cx="10" cy="10" r="5" fill="none" stroke="var(--white)" stroke-width="1.2"/><ellipse cx="10" cy="10" rx="2.2" ry="5" fill="none" stroke="var(--white)" stroke-width="1"/><line x1="5" y1="10" x2="15" y2="10" stroke="var(--white)" stroke-width="1"/></svg>
      </div>
    </div>

    <ul class="contact-list">
      <li>044-555 018 274</li>
      <li>info@tidewellevents.com</li>
      <li>www.tidewellevents.com</li>
    </ul>

    <div class="rule"></div>

    <p class="services">Disc Jockey Service | Photo Booth Rentals | Uplighting</p>
    <div class="card__edge"></div>
  </section>

</main>
</body>
</html>
```